We need a complete design for our construction company KELTO CONSTRUCTION based in Auckland New Zealand, we need a logo, website, business card, vehicle design etc..
We are a mid to high-end construction company who work mostly on residential projects and some commercial.

What we want to see in the design;
Professional,
Architectural,
Simple,
Alternative,

We want the design to communicate professionalism, high quality wormanship and and quality service.

Target Market(s)

People looking for a quality building/ construction company

Industry/Entity Type

Construction Company

Contact Information for Business Card

KELTO CONSTRUCTION.co.nz
Lino Verasek
lino@keltoconstruction.example.nz
021 5807 462

Logo Text

KELTO CONSTRUCTION

Number of Pages Required

5+ page

Font styles to use
Sans Serif

Colors

Designer to choose colors to be used in the design.

Requirements
Must have
• Must appear high end, professional, quality, be simple, easy to use, give security to potential clients
Nice to have
• high-quality photos of our recent projects
• about us page
• blog page
• contact us page
• high quality content
Should not have
• should not be hard to use and have too much going on.

```html
<!DOCTYPE html>
<html lang="en">
<head>
<meta charset="utf-8">
<title>Kelto Construction</title>
<link href="https://fonts.googleapis.com/css2?family=Montserrat:wght@400;500;600;700;800&display=swap" rel="stylesheet">
<style>
:root{
  --yellow:#f7b21b;
  --navy:#1f2a3a;
  --navy-deep:#1a2332;
  --ink:#1b1b1b;
  --muted:#777;
  --white:#fff;
  --line:#3a4658;
}
*{box-sizing:border-box;margin:0;padding:0}
html,body{width:1200px;height:4018px;overflow:hidden}
body{font-family:'Montserrat',sans-serif;color:var(--ink);background:var(--white);position:relative}
.abs{position:absolute}
.btn-outline{position:absolute;border:2px solid var(--yellow);border-radius:30px;font-weight:600;font-size:16px;display:flex;align-items:center;justify-content:center;color:var(--ink);background:#fff;letter-spacing:.5px}
.accent{color:var(--yellow)}

/* header */
.site-header{top:0;left:0;width:1200px;height:100px;background:#fff}
.brand{left:100px;top:38px;display:flex;align-items:center;gap:12px;font-weight:700;font-size:26px;color:var(--navy)}
.brand-dot{width:30px;height:30px;border-radius:50%;background:var(--yellow)}
.topline{right:100px;top:22px;font-size:15px;font-weight:600;color:var(--navy);display:flex;gap:14px;align-items:center}
.topline i{display:inline-block;width:12px;height:12px;background:var(--yellow);margin-right:6px;border-radius:2px}
.main-nav{right:100px;top:56px;display:flex;gap:62px;font-size:17px;color:#333;align-items:center}
.main-nav .current{color:var(--yellow)}

/* hero */
.hero{top:100px;left:0;width:1200px;height:583px;overflow:hidden}
.hero-photo{position:absolute;inset:0;background:linear-gradient(180deg,#6b6a66 0%,#a89a80 45%,#7a6a55 70%,#3d3a36 100%)}
.hero-title{left:281px;width:639px;height:64px;background:var(--yellow);color:#fff;font-weight:800;font-size:48px;display:flex;align-items:center;justify-content:center;letter-spacing:1px}
.hero-sub{left:0;width:1200px;text-align:center;color:#fff;font-size:23px;font-weight:500}
.hero-arrow{top:378px;width:38px;height:48px;background:rgba(0,0,0,.5);display:flex;align-items:center;justify-content:center}
.dots{left:556px;display:flex;gap:6px}
.dots span{width:14px;height:14px;border-radius:50%;border:2px solid #fff;background:transparent}
.dots span.on{background:var(--yellow);border-color:var(--yellow)}

/* welcome */
.welcome-title{left:115px;top:760px;font-size:40px;font-weight:800;line-height:52px;color:var(--ink)}
.helmet{left:115px;top:884px;width:448px;height:335px;background:radial-gradient(ellipse at 40% 45%,#f7c21b 0%,#e9a90f 45%,#d8c9a8 75%,#fff 100%)}
.welcome-text{left:643px;top:758px;width:456px;font-size:13px;line-height:26px;color:var(--muted)}
.ticks{left:643px;top:926px;width:456px;list-style:none;font-size:13px;line-height:27.5px;color:var(--muted)}
.ticks li{display:flex;align-items:center;gap:14px}
.ticks li::before{content:"";width:12px;height:12px;border-radius:50%;background:var(--yellow);flex:none}

/* services band */
.service{top:1281px;height:386px;width:402px}
.service h3{font-size:32px;font-weight:600}
.service p{font-size:13.5px;line-height:26px}
.svc-res{left:0;background:var(--navy);color:#fff}
.svc-photo{left:402px;width:397px;background:linear-gradient(180deg,#5a2a2a 0%,#c24a24 50%,#f29a2e 100%)}
.svc-com{left:799px;width:401px;background:var(--yellow);color:#fff;text-align:right}
.icon-bld{position:absolute;width:56px;height:50px}
.svc-btn{position:absolute;height:38px;width:116px;border-radius:20px;font-size:14px;font-weight:600;display:flex;align-items:center;justify-content:center}

/* projects */
.sec-title{left:0;width:1200px;text-align:center;font-size:38px;font-weight:800}
.sec-sub{left:0;width:1200px;text-align:center;font-size:15px;color:var(--muted)}
.proj{position:absolute;width:496px;height:354px}

/* CTA */
.cta{top:2734px;left:0;width:1200px;height:147px;background:var(--navy)}
.cta-yellow{position:absolute;left:0;top:0;width:1200px;height:147px}
.cta-text{left:119px;top:36px;font-size:26px;font-weight:700;line-height:40px;color:#fff}
.cta-btn{left:838px;top:50px;width:245px;height:47px;border:2px solid var(--yellow);border-radius:30px;color:var(--yellow);font-size:19px;font-weight:600;display:flex;align-items:center;justify-content:center}

/* blog */
.post{position:absolute;width:500px;height:178px}
.post-img{position:absolute;left:0;top:0;width:200px;height:178px}
.post-body{position:absolute;left:218px;top:0;width:280px}
.post-title{font-size:16px;font-weight:500}
.post-title b{font-weight:800}
.post-meta{font-size:13px;color:var(--yellow);margin:8px 0 6px;display:flex;gap:14px}
.post-meta span::before{content:"";display:inline-block;width:9px;height:9px;background:var(--yellow);margin-right:6px;border-radius:2px}
.post-text{font-size:13.5px;line-height:21px;color:var(--muted)}
.post .btn-outline{left:218px;top:140px;width:116px;height:38px;font-size:13px}

/* footer */
.footer{top:3546px;left:0;width:1200px;height:472px;background:var(--navy)}
.foot-h{font-size:26px;font-weight:700;color:var(--yellow)}
.contact-row{position:absolute;left:99px;display:flex;align-items:center;gap:22px;color:#fff;font-size:16px;line-height:25px}
.contact-row .ic{width:48px;height:48px;border-radius:50%;background:var(--yellow);flex:none;display:flex;align-items:center;justify-content:center}
.field{position:absolute;border:1px solid var(--line);background:var(--navy-deep);color:#fff;font-size:14px;padding:10px 14px}
.send{left:482px;width:118px;height:38px;background:var(--yellow);color:#fff;font-weight:700;font-size:15px;display:flex;align-items:center;justify-content:center}
.copy{left:99px;color:#fff;font-size:13px}
.social{display:flex;gap:10px;right:100px}
.social span{width:36px;height:36px;border:2px solid #fff;border-radius:50%}
</style>
</head>
<body>

<header class="site-header abs">
  <div class="brand abs"><span class="brand-dot"></span>Kelto Construction</div>
  <div class="topline abs"><span><i></i>Call Us : 1 800 555 0142</span><span>|</span><span><i></i>Email Us : info@keltobuild.example.nz</span></div>
  <nav class="main-nav abs">
    <span class="current">Home</span><span>About us</span><span>Projects</span><span>Blog</span><span>Contact us</span>
    <svg width="18" height="18" viewBox="0 0 18 18"><circle cx="7.5" cy="7.5" r="5.5" fill="none" stroke="#f7b21b" stroke-width="2.5"/><line x1="11.5" y1="11.5" x2="16" y2="16" stroke="#f7b21b" stroke-width="2.5"/></svg>
  </nav>
</header>

<section class="hero abs">
  <div class="hero-photo" role="img" aria-label="City skyline at sunset over water"></div>
  <div class="hero-arrow abs" style="left:0"><svg width="12" height="18"><path d="M10 2 3 9l7 7" stroke="#fff" stroke-width="2.5" fill="none"/></svg></div>
  <div class="hero-arrow abs" style="right:0"><svg width="12" height="18"><path d="M2 2l7 7-7 7" stroke="#fff" stroke-width="2.5" fill="none"/></svg></div>
  <div class="hero-title abs" style="top:308px">KELTO CONSTRUCTION</div>
  <div class="hero-sub abs" style="top:386px">We are a mid to high-end construction company</div>
  <svg class="abs" style="left:0;top:470px" width="1200" height="113" viewBox="0 0 1200 113">
    <path d="M0 40 Q600 150 1200 40 L1200 113 L0 113Z" fill="#fff"/>
    <path d="M180 70 Q600 125 1020 70" fill="none" stroke="#1f2a3a" stroke-width="7"/>
  </svg>
  <div class="dots abs" style="top:518px"><span class="on"></span><span></span><span></span><span></span><span></span></div>
</section>

<h2 class="welcome-title abs">WELCOME TO<br><span class="accent">KELTO CONSTRUCTION</span></h2>
<div class="helmet abs" role="img" aria-label="Yellow hard hat with folding ruler and plans"></div>
<p class="welcome-text abs">Lorem ipsum dolor sit amet, consectetur adipiscing elit, sed do eiusmod tempor incididunt ut labore et dolore magna aliqua. Ut enim ad minim veniam, quis nostrud exercitation ullamco laboris nisi ut aliquip ex ea commodo consequat. Duis aute irure dolor in voluptate velit esse cillum dolore eu fugiat...</p>
<ul class="ticks abs">
  <li>Duis aute irure dolor in reprehenderit in voluptate</li>
  <li>Velit esse cillum dolore eu fugiat nulla pariatur</li>
  <li>Excepteur sint occaecat cm ipsum dolor sit amet,</li>
  <li>Consectetur adipiscing elit, sed do eiusmod tempor</li>
  <li>Incididunt ut labore et dolore magna imad minim</li>
  <li>Veniamquis nostrud exercitation ullamco laboris</li>
  <li>Nisi ut aliquip ex ea commodo consequa</li>
</ul>
<div class="btn-outline" style="left:643px;top:1152px;width:140px;height:43px">READ MORE</div>

<section class="service svc-res abs">
  <svg class="icon-bld" style="left:99px;top:54px" viewBox="0 0 56 50"><rect x="4" y="8" width="30" height="42" fill="#f7b21b"/><rect x="34" y="20" width="18" height="30" fill="#f7b21b"/><g fill="#1f2a3a"><rect x="9" y="14" width="6" height="6"/><rect x="22" y="14" width="6" height="6"/><rect x="9" y="27" width="6" height="6"/><rect x="22" y="27" width="6" height="6"/><rect x="39" y="27" width="6" height="6"/></g></svg>
  <h3 class="abs" style="left:96px;top:118px">Residential</h3>
  <p class="abs" style="left:99px;top:160px;width:290px">Nemo enim ipsam voluptatem quia voluptas sit aspernatur aut odit aut fugit, sed quia consequuntur magni dolores eos qui ratione voluptatem</p>
  <div class="svc-btn" style="left:99px;top:288px;background:var(--yellow);color:#fff">READ MORE</div>
</section>
<div class="service svc-photo abs" role="img" aria-label="Two builders in silhouette against a sunset construction site"></div>
<section class="service svc-com abs">
  <svg class="icon-bld" style="right:88px;top:54px" viewBox="0 0 56 50"><rect x="4" y="18" width="18" height="32" fill="#1f2a3a"/><rect x="22" y="4" width="30" height="46" fill="#1f2a3a"/><g fill="#f7b21b"><rect x="27" y="10" width="6" height="6"/><rect x="40" y="10" width="6" height="6"/><rect x="27" y="24" width="6" height="6"/><rect x="40" y="24" width="6" height="6"/><rect x="9" y="26" width="6" height="6"/></g></svg>
  <h3 class="abs" style="right:100px;top:118px">Commercial</h3>
  <p class="abs" style="right:100px;top:160px;width:290px">Nemo enim ipsam voluptatem quia voluptas sit aspernatur aut odit aut fugit, sed quia consequuntur magni dolores eos qui ratione voluptatem</p>
  <div class="svc-btn" style="right:100px;top:288px;background:var(--navy);color:#fff">READ MORE</div>
</section>

<h2 class="sec-title abs" style="top:1742px">OUR RECENT <span class="accent">PROJECTS</span></h2>
<p class="sec-sub abs" style="top:1798px">Lorem ipsum dolor sit amet, consectetur adipiscing el sed do eiusmod tempor</p>
<div class="proj" style="left:99px;top:1844px;background:linear-gradient(180deg,#e9c05a,#d6a93a)" role="img" aria-label="Family home with yellow hover overlay">
  <svg class="abs" style="left:223px;top:120px" width="50" height="100" viewBox="0 0 50 100"><circle cx="25" cy="25" r="24" fill="#1f2a3a"/><circle cx="23" cy="23" r="8" fill="none" stroke="#fff" stroke-width="3"/><line x1="29" y1="29" x2="35" y2="35" stroke="#fff" stroke-width="3"/><circle cx="25" cy="75" r="22" fill="none" stroke="#fff" stroke-width="2"/><circle cx="25" cy="75" r="6" fill="none" stroke="#fff" stroke-width="2"/></svg>
</div>
<div class="proj" style="left:605px;top:1844px;background:linear-gradient(180deg,#4a8fd6 0%,#9ab8c8 45%,#7a6a58 65%,#5d8f3a 100%)" role="img" aria-label="Two-storey house with green lawn"></div>
<div class="proj" style="left:99px;top:2207px;background:linear-gradient(180deg,#9cc0e0 0%,#e8e4da 40%,#d6d0c2 80%,#555 100%)" role="img" aria-label="White townhouse with garages"></div>
<div class="proj" style="left:605px;top:2207px;background:linear-gradient(135deg,#6c95c8 0%,#b4c8da 45%,#c95a32 75%,#8a8a8a 100%)" role="img" aria-label="Modern building facade with glass and orange panels"></div>
<div class="btn-outline" style="left:485px;top:2600px;width:228px;height:48px;font-size:15px">VIEW MORE PROJECTS</div>

<section class="cta abs">
  <svg class="cta-yellow" viewBox="0 0 1200 147"><path d="M0 0H735L800 73 735 147H0Z" fill="#f7b21b"/></svg>
  <p class="cta-text abs">LOOKING FOR A QUALITY AND AFFORDABLE<br>CONSTRUCTOR FOR YOUR <span style="font-size:30px">NEXT PROJECT?</span></p>
  <div class="cta-btn abs">REQUEST A QUOTE</div>
</section>

<h2 class="sec-title abs" style="top:2956px">OUR <span class="accent">BLOG</span></h2>
<p class="sec-sub abs" style="top:3012px">Lorem ipsum dolor sit amet, consectetur adipiscing el sed do eiusmod tempor</p>

<article class="post" style="left:96px;top:3074px">
  <div class="post-img" style="background:linear-gradient(180deg,#7aa6d2,#e7b33a 60%,#9a7a55)" role="img" aria-label="Hard hat and tools on a building site"></div>
  <div class="post-body"><h4 class="post-title"><b>16 MAR :</b> VOLUPTIA VOLUPTAS SIT</h4><div class="post-meta"><span>By admin</span><span>Comments</span></div><p class="post-text">Lorem ipsum. Proin gravida nibh vel velit auctor aliquet. Aenean sollicitudin, lorem quis bi bendum auctor, nisi elit</p></div>
  <div class="btn-outline">READ MORE</div>
</article>
<article class="post" style="left:622px;top:3074px">
  <div class="post-img" style="background:linear-gradient(180deg,#c9d6e2,#a8a8a0 50%,#4f7a3a)" role="img" aria-label="Apartment block beside a garden path"></div>
  <div class="post-body"><h4 class="post-title"><b>18 MAR :</b> EXCEPTEURT ATATNON</h4><div class="post-meta"><span>By admin</span><span>Comments</span></div><p class="post-text">Lorem ipsum. Proin gravida nibh vel velit auctor aliquet. Aenean sollicitudin, lorem quis bi bendum auctor, nisi elit</p></div>
  <div class="btn-outline">READ MORE</div>
</article>
<article class="post" style="left:96px;top:3286px">
  <div class="post-img" style="background:linear-gradient(180deg,#5a8fd0,#e0a050 55%,#3a3a3a)" role="img" aria-label="Apartment balconies under blue sky"></div>
  <div class="post-body"><h4 class="post-title"><b>16 MAR :</b> EXCEPTEUR SINT OCCAE</h4><div class="post-meta"><span>By admin</span><span>Comments</span></div><p class="post-text">Lorem ipsum. Proin gravida nibh vel velit auctor aliquet. Aenean sollicitudin, lorem quis bi bendum auctor, nisi elit</p></div>
  <div class="btn-outline">READ MORE</div>
</article>
<article class="post" style="left:622px;top:3286px">
  <div class="post-img" style="background:linear-gradient(180deg,#6a9ad0,#3a4a5a 60%,#2a2f38)" role="img" aria-label="Modern glass office building"></div>
  <div class="post-body"><h4 class="post-title"><b>16 MAR :</b> VOLUPTIA VOLUPTAS SIT</h4><div class="post-meta"><span>By admin</span><span>Comments</span></div><p class="post-text">Lorem ipsum. Proin gravida nibh vel velit auctor aliquet. Aenean sollicitudin, lorem quis bi bendum auctor, nisi elit</p></div>
  <div class="btn-outline">READ MORE</div>
</article>

<footer class="footer abs">
  <h3 class="foot-h abs" style="left:99px;top:50px">Contact Us</h3>
  <div class="abs" style="left:99px;top:88px;width:106px;height:2px;background:var(--yellow)"></div>
  <div class="contact-row" style="top:130px"><span class="ic"><svg width="18" height="22" viewBox="0 0 18 22"><path d="M9 1a7 7 0 0 0-7 7c0 5 7 13 7 13s7-8 7-13a7 7 0 0 0-7-7z" fill="none" stroke="#fff" stroke-width="2"/><circle cx="9" cy="8" r="2.5" fill="#fff"/></svg></span><span>85,quis nostrud exercitation<br>ullamco labors.</span></div>
  <div class="contact-row" style="top:208px"><span class="ic"><svg width="22" height="16" viewBox="0 0 22 16"><rect x="1" y="1" width="20" height="14" fill="none" stroke="#fff" stroke-width="2"/><path d="M1 1l10 8 10-8" fill="none" stroke="#fff" stroke-width="2"/></svg></span><span>info@keltobuild.example.nz</span></div>
  <div class="contact-row" style="top:288px"><span class="ic"><svg width="20" height="20" viewBox="0 0 20 20"><path d="M4 1l4 4-2 3c1 3 3 5 6 6l3-2 4 4-3 3C8 19 1 12 1 4z" fill="none" stroke="#fff" stroke-width="2"/></svg></span><span>1 - 800 - 555 - 0142</span></div>

  <h3 class="foot-h abs" style="left:482px;top:40px;font-weight:600">Fill out the form below</h3>
  <div class="field" style="left:482px;top:102px;width:295px;height:43px">First Name</div>
  <div class="field" style="left:809px;top:102px;width:290px;height:43px">Last Name</div>
  <div class="field" style="left:482px;top:158px;width:295px;height:40px">Phone Number</div>
  <div class="field" style="left:809px;top:158px;width:290px;height:40px">E-Mail Address</div>
  <div class="field" style="left:482px;top:211px;width:617px;height:84px">Message</div>
  <div class="send abs" style="top:316px">Send Now</div>

  <div class="abs" style="left:0;top:394px;width:1200px;height:1px;background:var(--line)"></div>
  <p class="copy abs" style="top:425px">Copyright © 2018 Kelto Construction.All rights reserved</p>
  <div class="social abs" style="top:414px"><span></span><span></span><span></span></div>
</footer>

</body>
</html>
```